Dovetree baby skincare

design business cards (double sided) and complimentary note (single sided)

Industry/Entity Type

Business

Colors

Designer to choose colors to be used in the design.

```html
<!DOCTYPE html>
<html lang="en">
<head>
<meta charset="utf-8">
<title>Dovetree baby skincare – business card</title>
<link rel="stylesheet" href="https://fonts.googleapis.com/css2?family=Open+Sans:wght@400;700&display=swap">
<style>
  :root {
    --backdrop: #e9e9e7;
    --card: #fbfbfa;
    --card-edge: #e2e2df;
    --gold: #c9a233;
    --ink: #3a3a3a;
    --blush-1: #f3d2bf;
    --blush-2: #f8e4d8;
  }
  * { box-sizing: border-box; margin: 0; padding: 0; }
  html, body {
    width: 1200px;
    height: 800px;
    overflow: hidden;
    background: var(--backdrop);
    font-family: "Open Sans", Arial, sans-serif;
  }
  .canvas {
    position: relative;
    width: 1200px;
    height: 800px;
    display: flex;
    align-items: center;
    justify-content: center;
    gap: 60px;
  }
  .card {
    position: relative;
    width: 500px;
    height: 286px;
    background: var(--card);
    border: 1px solid var(--card-edge);
    box-shadow: 0 6px 18px rgba(0, 0, 0, 0.08);
    overflow: hidden;
  }
  .wordmark {
    position: absolute;
    font-weight: 700;
    color: var(--gold);
    letter-spacing: -0.5px;
    line-height: 1;
  }
  .card--front .wordmark {
    font-size: 64px;
    left: 50%;
    top: 50%;
    transform: translate(-50%, -50%);
  }
  .card--back .wordmark {
    font-size: 52px;
    left: 118px;
    top: 72px;
  }
  .blush-swatch {
    position: absolute;
    left: 330px;
    top: 20px;
    width: 100px;
    height: 130px;
    border-radius: 30px 44px 36px 26px;
    background: linear-gradient(180deg, var(--blush-1) 0%, var(--blush-2) 100%);
    opacity: 0.85;
  }
  .contact {
    position: absolute;
    left: 32px;
    bottom: 26px;
    color: var(--ink);
    font-size: 12.5px;
    line-height: 1.45;
  }
  .contact__name {
    font-size: 19px;
    font-weight: 400;
    margin-bottom: 2px;
  }
</style>
</head>
<body>
  <main class="canvas">
    <section class="card card--front" aria-label="Business card front">
      <span class="wordmark">dovetree</span>
    </section>

    <section class="card card--back" aria-label="Business card back">
      <div class="blush-swatch" role="img" aria-label="Soft peach watercolour brush stroke"></div>
      <span class="wordmark">dovetree</span>
      <div class="contact">
        <p class="contact__name">Maren Holt-Ashby</p>
        <p class="contact__role">CEO</p>
        <p class="contact__phone">61 (02) 95550147</p>
        <p class="contact__mobile">61400555219</p>
        <p class="contact__email">maren@dovetreeskincare.com</p>
        <p class="contact__web">www.dovetreeskincare.com</p>
      </div>
    </section>
  </main>
</body>
</html>
```